Web Design Project

I need a three page website. I have designed the index.html and the specialevent.html page.

I need someone to finetune the pages for me.

Where I have difficulty is with the following:
I want to add an event table driven by php database.
The administrator of the event will login and create the wording that fits under each colmn. The administrator the submit the form to php database. The database then display in a html.

The Table contains 5 coloums and the rows can vary and can go up to as many as 100.

The table set out events on a program
In the last column of every row I need a submit button to "View and Book" I need to link those buttons with external links/pages.

I use Dreamweaver CS5 and I need to have it in this format in order for me to edit it in the future.

The Table needs to be updated once a year for this program. So ideally if someone has a password to update the certain regions this is what I have in mind.

I have also designed a mockup of the restaurant page. At the top I need.
1) 4 Colapsable panels
a) Restaurants - opening the names of the restaurants
b) Coffee shops and light lunches .... with the names
c) Family
d) Home eateries

From the colapsable panel of each of these I need a anchored link to the description/photos of each...with a BOOK now button I can submit bookings to.

I added a colapsable panel in each restaurants description to keep everything contained.

Please help

• Background must be fixed so that main.div scroll over it

The colours are chosen so please stick to it.

The green for the submit button I short is. #C8D707

I need to edit the pages in Dreamweaver CS5. /Flexilayout2pro

Please ask if you need to know anything. I exactly know what I want.

Kind regards
Pieter Vansloten

The colours are fine.

The wording " karoovistadirect BOOKING agent" should appear right at the top in the white horizon part of the background image.

The specialevent page I described already. I am interested in the editable solution. for this.

I will make up a mockup of the third page and send it later.

Regards

```html
<!DOCTYPE html>
<html lang="en">
<head>
<meta charset="utf-8">
<title>Karoo Vista Direct – Food &amp; Drink</title>
<link href="https://fonts.googleapis.com/css2?family=Ubuntu:wght@400;500&family=Open+Sans:wght@300;400&display=swap" rel="stylesheet">
<style>
:root{
  --lime:#c8d707;
  --lime-deep:#b4c204;
  --lime-pale:#e4ec8a;
  --ink:#2f2f14;
  --text:#555;
  --muted:#8a8a8a;
  --dark:#34322c;
  --white:#fff;
  --rule:#e2e2e2;
}
*{box-sizing:border-box;margin:0;padding:0}
html,body{width:833px;height:1200px;overflow:hidden;background:var(--dark)}
body{font-family:"Open Sans",sans-serif;color:var(--text);position:relative}
.abs{position:absolute}
.backdrop{left:0;top:0;width:833px;height:522px;
  background:linear-gradient(180deg,#fff 0,#fff 70px,#b9b9b6 95px,#8f8f8a 150px,#6e6d68 260px,#8c8b86 380px,#5d5c57 522px)}
.brand{left:72px;top:48px;font-family:"Ubuntu",sans-serif;font-size:27px;color:var(--lime-deep);font-weight:400}
.nav{left:70px;top:99px;width:698px;height:40px;border-radius:20px;background:var(--lime);box-shadow:0 2px 3px rgba(0,0,0,.25)}
.nav a{position:absolute;top:0;height:40px;line-height:40px;color:var(--white);font-family:"Ubuntu",sans-serif;font-size:15px;text-decoration:none}
.nav .sep{position:absolute;top:0;width:1px;height:40px;background:rgba(255,255,255,.45)}
.panel{left:70px;top:173px;width:692px;height:800px;background:var(--white);border-radius:6px 6px 0 0}
.lead{left:70px;width:692px;top:202px;text-align:center;font-family:"Ubuntu",sans-serif;font-size:26px;color:var(--ink)}
.section-title{left:109px;top:252px;font-family:"Ubuntu",sans-serif;font-size:19px;color:var(--ink)}
.card{top:286px;width:144px;height:156px;background:var(--white);border-radius:5px;box-shadow:0 0 4px rgba(0,0,0,.18);overflow:hidden}
.card h3{height:30px;line-height:30px;background:var(--lime);color:var(--white);font-family:"Ubuntu",sans-serif;font-weight:400;font-size:14px;padding-left:19px}
.card ul{list-style:none;margin:8px 18px 0 20px}
.card li{font-size:9.5px;color:#444;height:24.5px;line-height:24px;border-bottom:1px solid var(--rule);padding-left:9px;position:relative}
.card li:last-child{border-bottom:0}
.card li::before{content:"";position:absolute;left:0;top:8.5px;border-left:4px solid var(--lime-deep);border-top:3.5px solid transparent;border-bottom:3.5px solid transparent}
.card p{font-size:7.6px;line-height:14.8px;padding:11px 17px 0 18px;color:#666}
.venue{width:300px}
.venue h2{font-family:"Ubuntu",sans-serif;font-weight:400;font-size:20px;color:var(--ink);height:26px}
.thumbs{display:flex;gap:2px;margin-top:4px}
.thumb{width:68px;height:44px}
.thumb.field{background:linear-gradient(180deg,#6d8fc6 0,#b9c7d8 38%,#6b7a45 52%,#c7c915 70%,#a3a80e 100%)}
.thumb.bridge{background:linear-gradient(180deg,#3f4a2c 0,#6b6a42 45%,#8b8b80 65%,#4a4a40 100%)}
.venue p{font-size:7.6px;line-height:14.8px;color:var(--muted);margin-top:13px;font-weight:300}
.divider{left:102px;top:726px;width:581px;height:1px;background:var(--rule)}
.footer{left:70px;top:962px;width:692px;height:188px;border-radius:4px 4px 10px 10px;
  background:linear-gradient(180deg,#d5e012 0,#c8d707 45%,#b7c406 100%);border-top:4px solid var(--lime-pale)}
.footer h4{position:absolute;font-family:"Ubuntu",sans-serif;font-weight:400;font-size:16px;color:var(--ink)}
.footer .line{position:absolute;font-size:9px;color:var(--ink)}
.footer .phone{font-family:"Ubuntu",sans-serif;font-size:12.5px}
.field-input{position:absolute;left:359px;top:72px;width:147px;height:18px;border-radius:9px;background:var(--white);font-size:7.5px;color:#999;line-height:18px;padding-left:10px}
.subscribe{position:absolute;left:446px;top:96px;width:61px;height:19px;border-radius:10px;background:#f1f4c4;font-size:9.5px;color:var(--ink);text-align:center;line-height:19px;font-family:"Ubuntu",sans-serif}
.social{position:absolute;top:64px;width:20px;height:20px;border-radius:50%;background:#1f1f14}
.copyright{left:0;width:833px;top:1174px;text-align:center;font-size:8.5px;color:#9a9a90}
</style>
</head>
<body>
<div class="abs backdrop" role="img" aria-label="Black and white photograph of the Karoo hills and town rooftops under a pale horizon"></div>

<div class="abs brand">Karoo Vista Direct</div>

<nav class="abs nav">
  <a style="left:170px">Home</a><span class="sep" style="left:228px"></span>
  <a style="left:253px">Accommodation</a><span class="sep" style="left:376px"></span>
  <a style="left:400px">Play</a><span class="sep" style="left:450px"></span>
  <a style="left:472px">Contact</a>
</nav>

<div class="abs panel"></div>
<h1 class="abs lead" style="font-weight:500">Your booking agent for</h1>
<div class="abs section-title">Food &amp; Drink</div>

<div class="abs card" style="left:104px"><h3>Restaurants</h3>
  <ul><li>Red Dune Table</li><li>Olive Terrace</li><li>Studio Cafe</li><li>Vlakte Kombuis</li></ul></div>
<div class="abs card" style="left:259px"><h3>Home Eateries</h3>
  <p>Vivamus porttitor, g, purus nisi eleifend libero, a tempus libero lectus feugiat felis. Morbi diam mauris, viverra in, gravida eu, mattis in, ante Morbi eget arcu.</p></div>
<div class="abs card" style="left:415px"><h3>Family Steakhouse</h3>
  <p>Vivamus porttitor, g, purus nisi eleifend libero, a tempus libero lectus feugiat felis. Morbi diam mauris, viverra in, gravida eu, mattis in, ante Morbi eget arcu.</p></div>
<div class="abs card" style="left:570px"><h3>Take Aways</h3>
  <p>Vivamus porttitor, g, purus nisi eleifend libero, a tempus libero lectus feugiat felis. Morbi diam mauris, viverra in, gravida eu, mattis in, ante Morbi eget arcu.</p></div>

<section class="abs venue" style="left:96px;top:525px"><h2>Red Dune Table</h2>
  <div class="thumbs"><div class="thumb field" role="img" aria-label="Venue photo: yellow flower field under mountains"></div><div class="thumb bridge" role="img" aria-label="Venue photo: stone bridge under trees"></div><div class="thumb field" role="img" aria-label="Venue photo: yellow flower field under mountains"></div></div>
  <p>Lorem ipsum dolor sit amet, consectetuer adipiscing elit, sed diam nonummy nibh euismod tincidunt ut laoreet dolore magna aliquam erat volutpat. Ut wisi enim ad minim veniam, quis nostrud exerci tation ullamcorper suscipit lobortis nisl ut aliquip ex ea commodo consequat. Duis autem vel eum iriure dolor in hendrerit in vulputate velit esse molestie consequat, vel illum dolore eu feugiat nulla facilisis at vero eros et accumsan et iusto odio dignissim qui blandit praesent</p></section>
<section class="abs venue" style="left:436px;top:525px"><h2>Vlakte Kombuis</h2>
  <div class="thumbs"><div class="thumb field" role="img" aria-label="Venue photo: yellow flower field under mountains"></div><div class="thumb bridge" role="img" aria-label="Venue photo: stone bridge under trees"></div><div class="thumb field" role="img" aria-label="Venue photo: yellow flower field under mountains"></div></div>
  <p>Lorem ipsum dolor sit amet, consectetuer adipiscing elit, sed diam nonummy nibh euismod tincidunt ut laoreet dolore magna aliquam erat volutpat. Ut wisi enim ad minim veniam, quis nostrud exerci tation ullamcorper suscipit lobortis nisl ut aliquip ex ea commodo consequat. Duis autem vel eum iriure dolor in hendrerit in vulputate velit esse molestie consequat, vel illum dolore eu feugiat nulla facilisis at vero eros et accumsan et iusto odio dignissim qui blandit praesent</p></section>

<div class="abs divider"></div>

<section class="abs venue" style="left:101px;top:745px"><h2>Studio Cafe</h2>
  <div class="thumbs"><div class="thumb field" role="img" aria-label="Venue photo: yellow flower field under mountains"></div><div class="thumb bridge" role="img" aria-label="Venue photo: stone bridge under trees"></div><div class="thumb field" role="img" aria-label="Venue photo: yellow flower field under mountains"></div></div>
  <p>Lorem ipsum dolor sit amet, consectetuer adipiscing elit, sed diam nonummy nibh euismod tincidunt ut laoreet dolore magna aliquam erat volutpat. Ut wisi enim ad minim veniam, quis nostrud exerci tation ullamcorper suscipit lobortis nisl ut aliquip ex ea commodo consequat. Duis autem vel eum iriure dolor in hendrerit in vulputate velit esse molestie consequat, vel illum dolore eu feugiat nulla facilisis at vero eros et accumsan et iusto odio dignissim qui blandit praesent</p></section>
<section class="abs venue" style="left:441px;top:745px"><h2>Ridgeback Arms</h2>
  <div class="thumbs"><div class="thumb field" role="img" aria-label="Venue photo: yellow flower field under mountains"></div><div class="thumb bridge" role="img" aria-label="Venue photo: stone bridge under trees"></div><div class="thumb field" role="img" aria-label="Venue photo: yellow flower field under mountains"></div></div>
  <p>Lorem ipsum dolor sit amet, consectetuer adipiscing elit, sed diam nonummy nibh euismod tincidunt ut laoreet dolore magna aliquam erat volutpat. Ut wisi enim ad minim veniam, quis nostrud exerci tation ullamcorper suscipit lobortis nisl ut aliquip ex ea commodo consequat. Duis autem vel eum iriure dolor in hendrerit in vulputate velit esse molestie consequat, vel illum dolore eu feugiat nulla facilisis at vero eros et accumsan et iusto odio dignissim qui blandit praesent</p></section>

<footer class="abs footer">
  <h4 style="left:33px;top:30px">Contact Us</h4>
  <div class="line phone" style="left:34px;top:56px">0861 555 210</div>
  <div class="line" style="left:34px;top:79px">email: admin@karoovista.example</div>
  <div class="line" style="left:34px;top:96px">address: Kerk Lane, Vlakte Dorp</div>

  <h4 style="left:210px;top:30px">Services List</h4>
  <div class="line" style="left:212px;top:58px">Business Directory</div>
  <div class="line" style="left:212px;top:75px">Relevant links and websites</div>
  <div class="line" style="left:212px;top:92px">Emergency Numbers</div>

  <h4 style="left:359px;top:28px">Newsletter Sign Up</h4>
  <div class="line" style="left:359px;top:53px">Please sign up here for latest news</div>
  <div class="field-input">email address</div>
  <div class="subscribe">Subscribe</div>

  <h4 style="left:543px;top:27px">Get in Touch</h4>
  <span class="social" style="left:545px"></span><span class="social" style="left:567px"></span>
  <span class="social" style="left:589px"></span><span class="social" style="left:611px"></span>
</footer>

<div class="abs copyright">Copyright © 2013 Company Name.&nbsp; All right reserved.</div>
</body>
</html>
```